Business card design Needed for new logo / Construction business, home extensions and new builds

We need a business card design using our new logo files which i will attach to this project :)

We are a small construction business specialising in home extensions, new builds and property development. We are very ambitious and would appreciate professional and elegant designs for our new business card.

Very serious about using the services on MakerQuarry and recently acquired our new logo from here :)

Please get involved, i will feedback when i can as i am very busy but can respond daily, thanks

Target Market(s)

People that want to build onto their houses, new building developments or adding too their existing property

Industry/Entity Type

Construction

Contact Information for Business Card

Renwick Tolliver Construction, Lionel Ashby (Managing Director), Tel 07822254961, email - info@renwick-tolliver, www.renwick-tolliver.co.uk

Colors

Designer to choose colors to be used in the design.

Requirements
Must have
• I like a deep grey on the back please. A lot of you have provided black from and back, try mixing things up a little. The black looks cool 😎 Thanks

```html
<!DOCTYPE html>
<html lang="en">
<head>
<meta charset="utf-8">
<title>Renwick Tolliver Construction – Business Card</title>
<link href="https://fonts.googleapis.com/css2?family=Cinzel:wght@400;600&family=Montserrat:wght@400;500&display=swap" rel="stylesheet">
<style>
  :root {
    --backdrop: #d9d9d7;
    --card-white: #ffffff;
    --card-grey: #676767;
    --gold: #c99a2e;
    --gold-edge: #d4a23a;
    --ink: #2f2f2f;
    --divider: #b9b9b9;
  }
  * { box-sizing: border-box; margin: 0; padding: 0; }
  html, body { width: 1200px; height: 801px; overflow: hidden; }
  body {
    background: var(--backdrop);
    font-family: "Montserrat", Arial, sans-serif;
    position: relative;
  }
  .card {
    position: absolute;
    top: 232px;
    width: 520px;
    height: 336px;
    border-bottom: 3px solid var(--gold-edge);
    border-right: 2px solid var(--gold-edge);
    box-shadow: 0 14px 30px rgba(0,0,0,0.22);
  }
  .card--front { left: 50px; background: var(--card-white); }
  .card--back { left: 630px; background: var(--card-grey); }

  .brand {
    display: flex;
    align-items: center;
    justify-content: center;
    gap: 10px;
    font-family: "Cinzel", Georgia, serif;
    font-weight: 600;
    color: var(--gold);
    text-transform: uppercase;
    text-align: center;
    line-height: 1.15;
  }
  .brand__mark { flex: none; background: var(--gold); }
  .card--front .brand {
    position: absolute; top: 56px; left: 0; right: 0;
    font-size: 19px; letter-spacing: 1.5px;
  }
  .card--front .brand__mark { width: 12px; height: 12px; }

  .holder {
    position: absolute; left: 40px; top: 200px; width: 200px;
    text-align: right;
  }
  .holder__name {
    font-family: "Cinzel", Georgia, serif;
    font-size: 22px; color: var(--gold); letter-spacing: 1px;
  }
  .holder__role { font-size: 14px; color: var(--ink); margin-top: 4px; }

  .rule {
    position: absolute; left: 262px; top: 188px;
    width: 1px; height: 86px; background: var(--divider);
  }

  .contacts {
    position: absolute; left: 284px; top: 190px;
    list-style: none; font-size: 13px; color: var(--ink);
  }
  .contacts li { display: flex; align-items: center; gap: 8px; height: 27px; }
  .contacts svg { width: 12px; height: 12px; flex: none; }

  .card--back .brand {
    position: absolute; top: 0; bottom: 0; left: 0; right: 0;
    font-size: 28px; letter-spacing: 2px;
  }
  .card--back .brand__mark { width: 18px; height: 18px; }
</style>
</head>
<body>

<section class="card card--front" aria-label="Card front">
  <div class="brand">
    <span class="brand__mark"></span>
    <span class="brand__name">Renwick Tolliver<br>Construction</span>
  </div>

  <div class="holder">
    <p class="holder__name">Lionel Ashby</p>
    <p class="holder__role">Managing Director</p>
  </div>

  <div class="rule"></div>

  <ul class="contacts">
    <li>
      <svg viewBox="0 0 12 12" aria-hidden="true"><path d="M3 1 L5 3.5 L4 5 Q5 7 7 8 L8.5 7 L11 9 L9.5 11 Q5 11 1 5 Q1 2 3 1Z" fill="var(--gold)"/></svg>
      07822254961
    </li>
    <li>
      <svg viewBox="0 0 12 12" aria-hidden="true"><rect x="1" y="2.5" width="10" height="7" fill="var(--gold)"/><path d="M1 2.5 L6 6.5 L11 2.5" stroke="#fff" stroke-width="1" fill="none"/></svg>
      info@renwick-tolliver
    </li>
    <li>
      <svg viewBox="0 0 12 12" aria-hidden="true"><circle cx="6" cy="6" r="5" fill="var(--gold)"/><path d="M1 6 H11 M6 1 Q3 6 6 11 M6 1 Q9 6 6 11" stroke="#fff" stroke-width="0.8" fill="none"/></svg>
      www.renwick-tolliver.co.uk
    </li>
  </ul>
</section>

<section class="card card--back" aria-label="Card back">
  <div class="brand">
    <span class="brand__mark"></span>
    <span class="brand__name">Renwick Tolliver<br>Construction</span>
  </div>
</section>

</body>
</html>
```